Business Cards - Brightpath Horizon

need to design unique business card for my mortgage business. I need to design credit card style business card for my business or any unique idea that you might have

Target Market(s)

Home Loan customers

Industry/Entity Type

Mortgage Brokerage

Contact Information for Business Card

please design credit card style or very unique style business card

Colors

Designer to choose colors to be used in the design.

Requirements
Must have
• Name
• position
• Phone number
• fax number
• email address
• website address
• social media address
• All above fields will be provided once design in finalised

```html
<!DOCTYPE html>
<html lang="en">
<head>
<meta charset="utf-8">
<title>Brightpath Horizon – Business Card</title>
<link rel="stylesheet" href="https://fonts.googleapis.com/css2?family=Crimson+Text:ital,wght@0,400;0,600;1,400&family=Orbitron:wght@400&display=swap">
<style>
  :root {
    --page-bg: #d9d9d9;
    --card-bg: #1d1e20;
    --card-edge: #2a2b2e;
    --brand-blue: #1f3fd1;
    --sky-blue: #2fa6e6;
    --accent-orange: #e88a1a;
    --text-light: #e6e6e6;
    --line-grey: #3a3b3e;
  }
  * { margin: 0; padding: 0; box-sizing: border-box; }
  html, body {
    width: 1200px; height: 901px; overflow: hidden;
    background: var(--page-bg);
  }
  .business-card {
    position: absolute; left: 100px; top: 140px;
    width: 1000px; height: 622px;
    background: var(--card-bg);
    border-radius: 28px;
    border: 1px solid var(--card-edge);
    font-family: "Crimson Text", Georgia, serif;
  }
  .brand-lockup { position: absolute; left: 66px; top: 150px; }
  .brand-name {
    font-size: 46px; font-weight: 400; line-height: 1;
    color: var(--brand-blue); letter-spacing: 1px;
  }
  .brand-tagline {
    margin-top: 14px; font-size: 21px; font-style: italic;
    color: var(--accent-orange);
  }
  .social-links {
    position: absolute; left: 749px; top: 75px;
    display: flex; gap: 6px;
  }
  .social-dot {
    width: 43px; height: 43px; border-radius: 50%;
    background: var(--brand-blue);
  }
  .card-number {
    position: absolute; left: 58px; top: 345px;
    font-family: "Orbitron", "Courier New", monospace;
    font-size: 62px; letter-spacing: 8px; word-spacing: 12px;
    color: var(--brand-blue);
  }
  .holder { position: absolute; left: 58px; top: 440px; }
  .holder-name {
    font-size: 36px; font-weight: 400; color: var(--brand-blue);
    line-height: 1.1; letter-spacing: .5px;
  }
  .holder-title {
    font-size: 27px; color: var(--accent-orange); line-height: 1.2;
    letter-spacing: .5px;
  }
  .home-illustration {
    position: absolute; left: 578px; top: 447px;
    width: 282px; height: 97px;
    background: linear-gradient(180deg, #26272a, #121314);
    border-radius: 4px;
  }
  .tree-illustration {
    position: absolute; left: 854px; top: 432px;
    width: 113px; height: 113px;
    background: radial-gradient(circle at 50% 40%, #3cb4f0, #1f8fd0);
    border-radius: 50% 50% 8px 8px;
  }
  .ground-line {
    position: absolute; left: 607px; top: 547px;
    width: 340px; height: 2px; background: var(--accent-orange);
  }
  .contact-line {
    position: absolute; left: 58px; top: 570px;
    display: flex; align-items: center;
    font-size: 25px; color: var(--text-light);
  }
  .contact-line .sep { margin: 0 12px; color: var(--text-light); }
  .phone-icon { width: 20px; height: 20px; margin-right: 12px; }
</style>
</head>
<body>
  <article class="business-card">
    <div class="brand-lockup">
      <div class="brand-name">Brightpath Horizon</div>
      <div class="brand-tagline">Right decision, Right time</div>
    </div>

    <nav class="social-links" aria-label="Social media">
      <span class="social-dot"></span>
      <span class="social-dot"></span>
      <span class="social-dot"></span>
      <span class="social-dot"></span>
    </nav>

    <div class="card-number">315 742 0968</div>

    <div class="holder">
      <div class="holder-name">DANIEL REYES</div>
      <div class="holder-title">CEO/FOUNDER</div>
    </div>

    <div class="home-illustration" role="img" aria-label="Embossed outline of house rooftops"></div>
    <div class="tree-illustration" role="img" aria-label="Blue tree illustration"></div>
    <div class="ground-line"></div>

    <div class="contact-line">
      <svg class="phone-icon" viewBox="0 0 24 24" aria-hidden="true">
        <path fill="#1f3fd1" d="M6.6 10.8a15.1 15.1 0 0 0 6.6 6.6l2.2-2.2c.3-.3.7-.4 1-.2 1.1.4 2.3.6 3.6.6.6 0 1 .4 1 1V20c0 .6-.4 1-1 1C10.6 21 3 13.4 3 4c0-.6.4-1 1-1h3.5c.6 0 1 .4 1 1 0 1.3.2 2.5.6 3.6.1.3 0 .7-.2 1z"/>
      </svg>
      <span>555 210 4816</span>
      <span class="sep">|</span>
      <span>hello@brightpathhorizon.com</span>
      <span class="sep">|</span>
      <span>www.brightpathhorizon.com</span>
    </div>
  </article>
</body>
</html>
```